Catering Menu Package

I currently have a complete menu package, which we have redesigned as far as content, now I need to it put together in a catalog type format. It is essentially 10-12 pages in length, and will be sent for print production. Upon receiving a final edit
Updates

I have added an example gif to the project.

I did this free hand this basically what I am looking for. please change text and type to whatever you think would look best. This is a total rough design so, feel free to change any and everything. The text for the page is on the word documents. If you need more images let me know I am in the process of getting as many images uploaded for your use.

Project Deadline Extended
Reason: I figured we got a late jump with questions, so i am extending a few days .

Target Market(s)

The target market is business who wish to have catered luncheons, breakfasts , meetings

Industry/Entity Type

Catering

Requirements
Must have
• I have attached a copy of the text that what we want in the package, our logo, and i have also attached a catering package of another company to give you an idea what the finished product will be
Should not have
• It should not look identical to the example catering packages, these are for some inspiration we want our own design with the same type of look and feel

```html
<!DOCTYPE html>
<html lang="en">
<head>
<meta charset="utf-8">
<title>Catering Menu – Sides, Salads &amp; Vegetables</title>
<link href="https://fonts.googleapis.com/css2?family=Pinyon+Script&family=Gabriela&display=swap" rel="stylesheet">
<style>
  :root {
    --paper: #ece4d6;
    --paper-edge: #e4dccd;
    --ink: #1c1a17;
    --produce-green: #3f6b2a;
    --produce-deep: #1f3a17;
    --produce-yellow: #d9b23a;
    --produce-red: #a8231c;
    --produce-cream: #e6d49a;
    --produce-purple: #6a1f5e;
  }
  * { margin: 0; padding: 0; box-sizing: border-box; }
  html, body { width: 1200px; height: 928px; overflow: hidden; background: var(--paper); }
  .menu-page {
    position: relative;
    width: 1200px;
    height: 928px;
    background: radial-gradient(ellipse at 60% 45%, var(--paper) 0%, var(--paper-edge) 100%);
    color: var(--ink);
    font-family: "Gabriela", serif;
    font-size: 15.7px;
    line-height: 21px;
  }
  .produce-panel {
    position: absolute;
    left: 0; top: 0;
    width: 370px; height: 928px;
    background:
      linear-gradient(180deg,
        var(--produce-deep) 0%,
        var(--produce-green) 12%,
        var(--produce-yellow) 24%,
        var(--produce-green) 36%,
        var(--produce-red) 44%,
        var(--produce-green) 54%,
        var(--produce-cream) 64%,
        var(--produce-cream) 74%,
        var(--produce-purple) 86%,
        var(--produce-deep) 100%);
  }
  .section-title {
    position: absolute;
    font-family: "Pinyon Script", cursive;
    font-weight: 400;
    font-size: 43px;
    line-height: 48px;
    color: var(--ink);
  }
  .block { position: absolute; left: 400px; }
  .price-row { display: flex; width: 720px; }
  .price-row .item { width: 584px; }
  .salad p { margin: 0; }
  .vegetables {
    position: absolute;
    right: 52px;
    text-align: right;
  }
  .vegetables ul { list-style: none; margin-top: 20px; }
</style>
</head>
<body>
<main class="menu-page">
  <div class="produce-panel" role="img" aria-label="Photograph of fresh produce: yellow squash, thyme sprigs, red and green peppers, fingerling potatoes and a purple orchid"></div>

  <h2 class="section-title" style="left:398px; top:84px;">Entr e Sides</h2>
  <div class="block" style="top:136px;">
    <div class="price-row"><span class="item">Fresh House Baked Rolls and Artisan Baguettes with Whipped Butter</span><span class="price">$&amp;.&amp;&amp; Per Dozen</span></div>
    <div class="price-row"><span class="item">Fresh Baked Garlic Bread</span><span class="price">$&amp;.&amp;&amp; Per Dozen</span></div>
  </div>

  <h2 class="section-title" style="left:398px; top:238px;">Fresh Salads</h2>
  <div class="block salad" style="top:286px;">
    <p>Tropical Salad-</p>
    <p>Customer Favorite! Spring Mix, Feta Cheese, Mandarin Oranges, and Dried Cranberries.Served with<br>our Fat-Free Raspberry Vinaigrette.</p>
  </div>
  <div class="block salad" style="top:370px;">
    <p>Classic Caeser Salad-</p>
    <p>Crisp Romaine Lettuce, Creamy Caesar Dressing, Garlic Croutons, and Imported Parmsan Cheese.</p>
  </div>
  <div class="block salad" style="top:433px;">
    <p>Roman Salad-</p>
    <p>Crisp Romaine Lettuce, Black Olives, Grape Tomatoes, Feta Cheese, and Red Onions.Served with<br>our Chef-made Parmesan-Pepper Dressing.</p>
  </div>
  <div class="block salad" style="top:517px;">
    <p>Farm Fresh Garden Salad-</p>
    <p>Spring Mix, Shredded Carrots, Grape Tomatoes, Cucumbers, Red Onions, and<br>Garlic Croutons.Accompanied with Ranch Dressing and our Chef-made Balsamic Dressing.</p>
  </div>

  <section class="vegetables" style="top:626px;">
    <h2 class="section-title" style="position:static;">Vegetable Substitutes</h2>
    <p>To substitute, free of charge, to add $&amp;.&amp;&amp;</p>
    <ul>
      <li>Lemon Scented Petit Green Beans</li>
      <li>Tomato-Zucchini Casserole</li>
      <li>Steamed Broccoli</li>
      <li>Maple Glazed Carrots</li>
      <li>Sautéed Local Corn</li>
    </ul>
  </section>
</main>
</body>
</html>
```